PWRPT design for Company

Project: Develop a pwrpt for QT7lx. This can be just a blank pwrpt with standard templates that we can use to build our content and solutions around.
Website: www.qt7lx.example
Color Pallet: Try to use the color schema from our website.
PWRPT Design Tips: While we are a research-based company, our primary target is schools and school districts. We say our work is RESEARCH, POLICY, AND PRACTICE. I would like images that represent “WHY” our research matters, i.e. students, teachers, and administrators. If you can use images and stock photos that represent students with diverse backgrounds, teachers that are diverse and clearly teaching, and administrators that run a school, university, etc. We are in the process of updating our website, but the color scheme will remain the same.
Additional Information:
We built, researched, and designed, www.brvo-kt.example .
We built, researched, and designed, http://67pwgamma.example/olar/index.html
Target Market(s)
EDUCATION
Industry/Entity Type
It Company
Look and feel

```html
<!DOCTYPE html>
<html lang="en">
<head>
<meta charset="utf-8">
<title>QT7lx Presentation Templates</title>
<link rel="stylesheet" href="https://fonts.googleapis.com/css2?family=Montserrat:wght@300;400;600;700;800&display=swap">
<style>
  :root{
    --canvas:#000;
    --paper:#ffffff;
    --ink:#2a2a2a;
    --body:#4a4a4a;
    --orange:#f26b3a;
    --orange-deep:#f0532f;
    --orange-soft:#f7805c;
    --amber:#f98a3c;
    --yellow:#fbd34a;
    --footer:#525d5c;
    --badge-grey:#c4c4c4;
  }
  *{box-sizing:border-box;margin:0;padding:0}
  html,body{width:1020px;height:1200px;overflow:hidden;background:var(--canvas)}
  body{position:relative;font-family:"Montserrat",sans-serif;color:var(--ink)}
  .slide{position:absolute;background:var(--paper);overflow:hidden}
  .col-left{left:16px;width:490px}
  .col-right{left:520px;width:485px}
  .row-1{top:16px;height:290px}
  .row-2{top:320px;height:276px}
  .row-3{top:610px;height:284px}
  .row-4{top:910px;height:274px}

  .deco{position:absolute;inset:0;width:100%;height:100%;pointer-events:none}
  .accent-bar{position:absolute;left:20px;top:14px;width:185px;height:2px;background:var(--yellow)}
  .slide-title{position:absolute;left:20px;top:30px;font-weight:800;font-size:15px;letter-spacing:.2px;color:var(--ink);white-space:nowrap}
  .slide-title em{font-style:normal;color:var(--orange)}
  .brand{position:absolute;right:8px;top:24px;display:flex;flex-direction:column;align-items:flex-end}
  .brand-name{display:flex;align-items:center;gap:4px;font-weight:400;font-size:15px;color:var(--ink);line-height:1}
  .brand-dot{width:9px;height:9px;border-radius:50%;background:var(--orange)}
  .brand-tag{font-size:3.4px;letter-spacing:.4px;color:#999;margin-top:2px}
  .footer{position:absolute;left:0;right:0;bottom:0;height:9px;background:var(--footer);color:#fff;font-size:5px;line-height:9px;padding-left:5px}

  .copy{position:absolute;font-size:6.1px;line-height:10.3px;color:var(--body);text-align:justify}
  .copy p+p{margin-top:10px}
  .col-title{font-weight:700;font-size:10.5px;color:var(--orange);line-height:14px}

  .photo{position:absolute}
  .photo-circle{border-radius:50%;background:radial-gradient(circle at 40% 35%,#e8d9cc,#a38470 60%,#5a4a44)}
  .ring{position:absolute;border-radius:50%;border:1px solid #f6b79a}
  .dot{position:absolute;border-radius:50%}

  .students-label{position:absolute;left:22px;top:156px;font-size:10.5px;color:#fff;font-weight:400}

  .partner-grid{position:absolute;left:20px;top:93px;width:200px}
  .badge-row{display:flex;gap:10px;margin-bottom:10px}
  .badge-round{width:34px;height:34px;border-radius:50%;background:var(--badge-grey)}
  .badge-bar{width:38px;height:12px;background:var(--badge-grey)}

  .icon-cols{position:absolute;left:42px;top:88px;display:flex;gap:30px}
  .icon-col{width:126px;text-align:center}
  .icon-col svg{width:40px;height:40px}
  .icon-title{font-weight:600;font-size:9.5px;color:var(--orange);margin:6px 0 5px}
  .icon-col .copy{position:static}

  .section{background:linear-gradient(100deg,#f26744 0%,#f47a5a 55%,#f26a4a 100%)}
  .section-title{position:absolute;left:29px;top:120px;font-weight:700;font-size:22.5px;color:#fff;letter-spacing:.3px}
  .section-sub{position:absolute;left:31px;top:148px;width:270px;font-size:5.4px;line-height:10px;color:#fff}
</style>
</head>
<body>

<section class="slide col-left row-1">
  <svg class="deco" viewBox="0 0 490 290"><circle cx="450" cy="140" r="190" fill="none" stroke="#fbe7a6" stroke-width=".8"/><circle cx="372" cy="55" r="4.5" fill="var(--orange)"/><circle cx="395" cy="272" r="4.5" fill="var(--orange)"/></svg>
  <div class="accent-bar"></div>
  <h1 class="slide-title">ABOUT <em>INTRODUCTION</em></h1>
  <div class="brand"><div class="brand-name"><span class="brand-dot"></span>QT7lx</div><div class="brand-tag">STUDY • PLAN • TEACH</div></div>
  <svg class="photo" style="left:0;top:60px" width="170" height="195" viewBox="0 0 170 195" role="img" aria-label="Photo of smiling students with orange tint">
    <defs><linearGradient id="tri" x1="0" y1="0" x2="1" y2="1"><stop offset="0" stop-color="#f59a6a"/><stop offset="1" stop-color="#ee6a34"/></linearGradient></defs>
    <path d="M18 2 Q5 0 5 15 L5 180 Q5 194 18 188 L160 110 Q170 97 160 86 Z" fill="url(#tri)"/>
  </svg>
  <div class="students-label">Our Students</div>
  <div class="copy" style="left:200px;top:86px;width:268px">
    <p>Lorem Ipsum is simply dummy text of the printing and typesetting industry. Lorem Ipsum has been the industry's standard dummy text ever since the 1500s, when an unknown printer took a galley of type and scrambled it to make a type specimen book. It has survived not only five centuries, but also the leap into electronic typesetting, remaining essentially unchanged. It was popularised in the 1960s with the release of Tessaline sheets containing Lorem Ipsum passages, and more recently with desktop publishing software like Orvo LayoutDesk including versions of Lorem Ipsum.</p>
    <p>Lorem Ipsum is simply dummy text of the printing and typesetting industry. Lorem Ipsum has been the industry's standard dummy text ever since the 1500s, when an unknown printer took a galley of type and scrambled it to make a type specimen book. It has survived not only five centuries, but also the leap into electronic typesetting, remaining essentially unchanged.</p>
    <p>It was popularised in the 1960s with the release of Tessaline sheets containing Lorem Ipsum passages, and more recently with desktop publishing software like Orvo LayoutDesk including versions of Lorem Ipsum.</p>
  </div>
  <div class="footer">Copyright @Text</div>
</section>

<section class="slide col-right row-1">
  <svg class="deco" viewBox="0 0 485 290"><circle cx="420" cy="120" r="160" fill="none" stroke="#fbe7a6" stroke-width=".8"/><circle cx="369" cy="55" r="4.5" fill="var(--yellow)"/><circle cx="392" cy="273" r="4.5" fill="var(--orange)"/></svg>
  <div class="accent-bar"></div>
  <h1 class="slide-title">TWO <em>COL CONTENT</em></h1>
  <div class="brand"><div class="brand-name"><span class="brand-dot"></span>QT7lx</div><div class="brand-tag">STUDY • PLAN • TEACH</div></div>
  <div class="copy" style="left:23px;top:77px;width:193px">
    <div class="col-title">Col Title</div>
    <p>Lorem Ipsum is simply dummy text of the printing and typesetting industry. Lorem Ipsum has been the industry's standard dummy text ever since the 1500s, when an unknown printer took a galley of type and scrambled it to make a type specimen book. It has survived not only five centuries, but also the leap into electronic typesetting, remaining essentially unchanged. Lorem Ipsum is simply dummy text of the printing and typesetting industry.</p>
    <p>Lorem Ipsum has been the industry's standard dummy text ever since the 1500s, when an unknown printer took a galley of type and scrambled it to make a type specimen book. It has survived not only five centuries, but also the leap into electronic typesetting, remaining essentially unchanged.</p>
  </div>
  <div class="copy" style="left:253px;top:91px;width:193px">
    <p>Lorem Ipsum is simply dummy text of the printing and typesetting industry. Lorem Ipsum has been the industry's standard dummy text ever since the 1500s, when an unknown printer took a galley of type and scrambled it to make a type specimen book. It has survived not only five centuries, but also the leap into electronic typesetting, remaining essentially unchanged. Lorem Ipsum is simply dummy text of the printing and typesetting industry.</p>
    <p>Lorem Ipsum has been the industry's standard dummy text ever since the 1500s, when an unknown printer took a galley of type and scrambled it to make a type specimen book. It has survived not only five centuries, but also the leap into electronic typesetting, remaining essentially unchanged.</p>
  </div>
  <div class="footer">Copyright @Text</div>
</section>

<section class="slide col-left row-2">
  <svg class="deco" viewBox="0 0 490 276"><circle cx="450" cy="130" r="190" fill="none" stroke="#fbe7a6" stroke-width=".8"/><circle cx="372" cy="42" r="4.5" fill="var(--orange)"/><circle cx="395" cy="259" r="4.5" fill="var(--orange)"/></svg>
  <div class="accent-bar"></div>
  <h1 class="slide-title">OUR <em>PARTNER</em></h1>
  <div class="brand"><div class="brand-name"><span class="brand-dot"></span>QT7lx</div><div class="brand-tag">STUDY • PLAN • TEACH</div></div>
  <div class="partner-grid" role="img" aria-label="Partner badges">
    <div class="badge-row"><span class="badge-round"></span><span class="badge-round" style="width:46px"></span><span class="badge-round"></span><span class="badge-round"></span></div>
    <div class="badge-row"><span class="badge-bar"></span><span class="badge-bar" style="width:50px"></span><span class="badge-bar" style="width:28px"></span><span class="badge-bar" style="width:30px"></span></div>
    <div class="badge-row" style="padding-left:38px"><span class="badge-bar" style="width:32px;height:16px"></span><span class="badge-bar" style="width:64px"></span></div>
  </div>
  <div class="copy" style="left:232px;top:76px;width:235px">
    <p>Lorem Ipsum is simply dummy text of the printing and typesetting industry. Lorem Ipsum has been the industry's standard dummy text ever since the 1500s, when an unknown printer took a galley of type and scrambled it to make a type specimen book. It has survived not only five centuries, but also the leap into electronic typesetting, remaining essentially unchanged. It was popularised in the 1960s with the release of Tessaline sheets containing Lorem Ipsum passages, and more recently with desktop publishing software like Orvo LayoutDesk including versions of Lorem Ipsum.</p>
    <p>Lorem Ipsum is simply dummy text of the printing and typesetting industry. Lorem Ipsum has been the industry's standard dummy text ever since the 1500s, when an unknown printer took a galley of type and scrambled it to make a type specimen book. It has survived not only five centuries, but also the leap into electronic typesetting, remaining essentially unchanged.</p>
  </div>
  <div class="footer">Copyright @Text</div>
</section>

<section class="slide col-right row-2">
  <svg class="deco" viewBox="0 0 485 276"><circle cx="420" cy="110" r="160" fill="none" stroke="#fbe7a6" stroke-width=".8"/></svg>
  <div class="accent-bar"></div>
  <h1 class="slide-title">OUR <em>GRAPHICS</em></h1>
  <div class="brand"><div class="brand-name"><span class="brand-dot"></span>QT7lx</div><div class="brand-tag">STUDY • PLAN • TEACH</div></div>
  <svg class="deco" viewBox="0 0 485 276" font-family="Montserrat,sans-serif" text-anchor="middle">
    <g stroke-linejoin="round" stroke-width="10">
      <polygon points="230,42 182,122 278,122" fill="var(--orange-deep)" stroke="var(--orange-deep)"/>
      <polygon points="182,142 278,142 230,222" fill="var(--amber)" stroke="var(--amber)"/>
      <polygon points="160,160 114,236 206,236" fill="var(--orange-soft)" stroke="var(--orange-soft)"/>
      <polygon points="296,160 250,236 342,236" fill="var(--yellow)" stroke="var(--yellow)"/>
    </g>
    <g fill="#fff">
      <text x="230" y="102" font-size="18" font-weight="800">K2</text>
      <text x="230" y="115" font-size="7.2">EDUCATION</text>
      <text x="230" y="124" font-size="7.2">SYSTEM</text>
      <text x="228" y="161" font-size="18" font-weight="800">200 B</text>
      <text x="230" y="173" font-size="7.2">ANNUAL</text>
      <text x="230" y="182" font-size="7.2">SPENDING</text>
      <text x="160" y="208" font-size="17" font-weight="800">3 M</text>
      <text x="160" y="221" font-size="7.2">TEACHER</text>
      <text x="296" y="191" font-size="15" font-weight="800">NO</text>
      <text x="296" y="210" font-size="15" font-weight="800">COST</text>
      <text x="296" y="222" font-size="7.2">CONSULTATION</text>
    </g>
  </svg>
  <div class="footer">Copyright @Text</div>
</section>

<section class="slide col-left row-3">
  <svg class="deco" viewBox="0 0 490 284"><circle cx="470" cy="100" r="170" fill="none" stroke="#fbe7a6" stroke-width=".8"/></svg>
  <div class="accent-bar"></div>
  <h1 class="slide-title">ONE <em>COL CONTENT</em></h1>
  <div class="brand"><div class="brand-name"><span class="brand-dot"></span>QT7lx</div><div class="brand-tag">STUDY • PLAN • TEACH</div></div>
  <div class="copy" style="left:23px;top:66px;width:195px">
    <div class="col-title">Col Title</div>
    <p>Lorem Ipsum is simply dummy text of the printing and typesetting industry. Lorem Ipsum has been the industry's standard dummy text ever since the 1500s, when an unknown printer took a galley of type and scrambled it to make a type specimen book. It has survived not only five centuries, but also the leap into electronic typesetting, remaining essentially unchanged. Lorem Ipsum is simply dummy text of the printing and typesetting industry.</p>
    <p>Lorem Ipsum has been the industry's standard dummy text ever since the 1500s, when an unknown printer took a galley of type and scrambled it to make a type specimen book. It has survived not only five centuries, but also the leap into electronic typesetting, remaining essentially unchanged.</p>
  </div>
  <div class="ring" style="left:264px;top:65px;width:170px;height:170px"></div>
  <div class="photo photo-circle" role="img" aria-label="Photo of two students studying together at a desk" style="left:270px;top:72px;width:158px;height:158px"></div>
  <div class="dot" style="left:299px;top:82px;width:13px;height:13px;background:var(--yellow)"></div>
  <div class="dot" style="left:399px;top:209px;width:16px;height:16px;background:var(--orange)"></div>
  <div class="footer">Copyright @Text</div>
</section>

<section class="slide col-right row-3">
  <svg class="deco" viewBox="0 0 485 284"><circle cx="430" cy="90" r="150" fill="none" stroke="#fbe7a6" stroke-width=".8"/></svg>
  <div class="accent-bar"></div>
  <h1 class="slide-title">TWO <em>COL CONTENT</em></h1>
  <div class="brand"><div class="brand-name"><span class="brand-dot"></span>QT7lx</div><div class="brand-tag">STUDY • PLAN • TEACH</div></div>
  <div class="copy" style="left:21px;top:66px;width:268px">
    <div class="col-title">Col Title</div>
    <p>Lorem Ipsum is simply dummy text of the printing and typesetting industry. Lorem Ipsum has been the industry's standard dummy text ever since the 1500s, when an unknown printer took a galley of type and scrambled it to make a type specimen book. It has survived not only five centuries, but also the leap into electronic typesetting, remaining essentially unchanged. Lorem Ipsum is simply dummy text of the printing and typesetting industry.</p>
  </div>
  <div class="copy" style="left:21px;top:167px;width:268px">
    <div class="col-title">Col Title</div>
    <p>Lorem Ipsum is simply dummy text of the printing and typesetting industry. Lorem Ipsum has been the industry's standard dummy text ever since the 1500s, when an unknown printer took a galley of type and scrambled it to make a type specimen book. It has survived not only five centuries, but also the leap into electronic typesetting, remaining essentially unchanged. Lorem Ipsum is simply dummy text of the printing and typesetting industry.</p>
  </div>
  <div class="ring" style="left:303px;top:57px;width:98px;height:98px"></div>
  <div class="photo photo-circle" role="img" aria-label="Photo of two students reading at a table" style="left:307px;top:61px;width:90px;height:90px"></div>
  <div class="ring" style="left:297px;top:169px;width:98px;height:98px"></div>
  <div class="photo photo-circle" role="img" aria-label="Photo of a group of smiling students in a library" style="left:301px;top:173px;width:90px;height:90px"></div>
  <div class="dot" style="left:362px;top:263px;width:8px;height:8px;background:var(--orange)"></div>
  <div class="dot" style="left:364px;top:50px;width:8px;height:8px;background:var(--yellow)"></div>
  <div class="footer">Copyright @Text</div>
</section>

<section class="slide col-left row-4">
  <div class="accent-bar"></div>
  <h1 class="slide-title">OUR <em>GRAPHICS</em></h1>
  <div class="brand"><div class="brand-name"><span class="brand-dot"></span>QT7lx</div><div class="brand-tag">STUDY • PLAN • TEACH</div></div>
  <div class="icon-cols">
    <div class="icon-col">
      <svg viewBox="0 0 40 40" fill="none" stroke="var(--orange)" stroke-width="1.3"><rect x="2" y="2" width="36" height="36"/><line x1="2" y1="9" x2="38" y2="9"/><line x1="8" y1="16" x2="26" y2="16"/><line x1="8" y1="22" x2="26" y2="22"/><line x1="8" y1="28" x2="26" y2="28"/><circle cx="32" cy="18" r="1.5"/><circle cx="32" cy="24" r="1.5"/><circle cx="32" cy="30" r="1.5"/></svg>
      <div class="icon-title">ICONS TITLE HERE</div>
      <div class="copy">Lorem Ipsum is simply dummy text of the printing and typesetting industry. Lorem Ipsum has been the industry's standard dummy text ever since the 1500s, when an unknown printer took a galley of type and scrambled it to make a type specimen book. It has survived not only five centuries, but also the leap into electronic typesetting, remaining essentially</div>
    </div>
    <div class="icon-col">
      <svg viewBox="0 0 40 40" fill="none" stroke="var(--orange)" stroke-width="1.3"><path d="M13 17 V11 a7 7 0 0 1 14 0 V17"/><path d="M8 17 H32 V28 Q32 36 20 38 Q8 36 8 28 Z"/><circle cx="20" cy="25" r="3"/><line x1="20" y1="28" x2="20" y2="32"/></svg>
      <div class="icon-title">ICONS TITLE HERE</div>
      <div class="copy">Lorem Ipsum is simply dummy text of the printing and typesetting industry. Lorem Ipsum has been the industry's standard dummy text ever since the 1500s, when an unknown printer took a galley of type and scrambled it to make a type specimen book. It has survived not only five centuries, but also the leap into electronic typesetting, remaining essentially</div>
    </div>
    <div class="icon-col">
      <svg viewBox="0 0 40 40" fill="none" stroke="var(--orange)" stroke-width="1.3"><rect x="3" y="4" width="34" height="22"/><polyline points="7,21 14,14 19,18 26,10 33,13"/><line x1="20" y1="26" x2="12" y2="37"/><line x1="20" y1="26" x2="28" y2="37"/><line x1="20" y1="26" x2="20" y2="34"/></svg>
      <div class="icon-title">ICONS TITLE HERE</div>
      <div class="copy">Lorem Ipsum is simply dummy text of the printing and typesetting industry. Lorem Ipsum has been the industry's standard dummy text ever since the 1500s, when an unknown printer took a galley of type and scrambled it to make a type specimen book. It has survived not only five centuries, but also the leap into electronic typesetting, remaining essentially</div>
    </div>
  </div>
  <div class="footer">Copyright @Text</div>
</section>

<section class="slide col-right row-4 section" role="img" aria-label="Orange-tinted photo of a group of smiling students">
  <svg class="deco" viewBox="0 0 485 274"><circle cx="500" cy="20" r="150" fill="none" stroke="#ffd3a0" stroke-width=".8"/><circle cx="368" cy="40" r="4.5" fill="var(--yellow)"/></svg>
  <h1 class="section-title">SECTION TITLE HERE</h1>
  <p class="section-sub">Lorem Ipsum is simply dummy text of the printing and typesetting industry. Lorem Ipsum has been the industry's standard dummy text ever since the 1500s.</p>
</section>

</body>
</html>
```